wardrobe/costume stylist needs good business card for own business

Hi:)

I'm wanting a business card for my company. I am a freelance stylist.

I do wardrobe/costume stylist to TV commercials; Films; Fashion and Lifestyle shoots.

I'd like a design based around my name Rosalind Parfrey written nicely, maybe a colour? Up to you?!

I've attached a couple of images of business cards I like
.... be creative and have fun!

Thank you :)

Reason: I was trying to get my new business card ready for before I headed overseas Friday morning but I don't think that was realistic so I'd like to extend the deadline to give time to the project. Thank you

Hi designers:) Thank you for all your designs, I've extended the deadline until Sunday, so there's a bit more time. I've attached 3 pictures of business cards which I quite like, please take a look to see if it can be of help in your process. I like the pale plain or patterned background with dark font and the dark plain or patterned background with the pale font the motifs the feminine fonts the plain fonts I like the idea of playing with a circle or some shape on one side of the card with my name or initials as in the picture I have on my post could you play around with this idea a bit please? Thank you all for the work you've done :) Rosa

Hi I am working overseas til Saturday night sorry for no feedback until I teturn Thanks :) Rosa

Hi designers, Thank you all so much for submitting your designs, I really appreciate your input into my project :) I'm sorry I didn't get to respond to some comments, and give feedback. I didn't back from being away until later than I expected, and the deadline had passed then, so apologies. Thanks to you all again for all your really good designs :) Rosa

Target Market(s)

I am a freelance stylist my target audience is producers, production companies, photographers, directors...

Industry/Entity Type

Business

Requirements
Must have
• Rosalind Parfrey
Stylist or Wardrobe Stylist

email rosaparfrey@mailbox-example.co.nz
Mobile 0218467193

(Don't have to use the words 'email' and 'mobile')
Nice to have
• Would like it to be double sided
Like B & W
Like pale colour background with dark font or white font
Like dark colour background with pale font
Should not have
• I would prefer it not to incorporate pictures

```html
<!DOCTYPE html>
<html lang="en">
<head>
<meta charset="utf-8">
<title>Rosalind Parfrey, Stylist: Business Card</title>
<link rel="stylesheet" href="https://fonts.googleapis.com/css2?family=Pinyon+Script&family=Encode+Sans+Condensed:wght@300;400&display=swap">
<style>
  :root {
    --page: #ffffff;
    --card: #b5b2a7;
    --ink-dark: #6b6b6b;
    --ink-light: #ffffff;
    --script: "Pinyon Script", cursive;
    --sans: "Encode Sans Condensed", sans-serif;
  }
  * { box-sizing: border-box; margin: 0; padding: 0; }
  html, body {
    width: 1000px;
    height: 1200px;
    overflow: hidden;
    background: var(--page);
  }
  .sheet {
    position: relative;
    width: 1000px;
    height: 1200px;
  }
  .card {
    position: absolute;
    left: 23px;
    width: 954px;
    height: 544px;
    background: var(--card);
  }
  .card--front { top: 44px; }
  .card--back { top: 612px; }

  .initials {
    position: absolute;
    font-family: var(--sans);
    font-weight: 300;
    color: var(--ink-dark);
    line-height: 1;
    letter-spacing: 4px;
  }
  .card--front .initials {
    right: 60px;
    top: 100px;
    font-size: 130px;
  }
  .card--back .initials {
    left: 150px;
    top: 130px;
    font-size: 110px;
  }

  .client-name {
    position: absolute;
    right: 80px;
    top: 240px;
    font-family: var(--script);
    font-weight: 400;
    font-size: 68px;
    color: var(--ink-dark);
    line-height: 1;
    white-space: nowrap;
  }
  .role {
    position: absolute;
    right: 83px;
    top: 336px;
    font-family: var(--sans);
    font-weight: 300;
    font-size: 50px;
    color: var(--ink-light);
    line-height: 1;
  }

  .contact {
    position: absolute;
    left: 257px;
    top: 262px;
    transform: translateX(-50%);
    text-align: center;
    font-family: var(--sans);
    font-weight: 300;
    color: var(--ink-dark);
    line-height: 1;
    white-space: nowrap;
  }
  .contact__email { font-size: 28px; display: block; }
  .contact__phone { font-size: 32px; display: block; margin-top: 16px; }
</style>
</head>
<body>
  <main class="sheet">
    <section class="card card--front" aria-label="Card front">
      <div class="initials">RP</div>
      <h1 class="client-name">Rosalind Parfrey</h1>
      <p class="role">Stylist</p>
    </section>

    <section class="card card--back" aria-label="Card back">
      <div class="initials">RP</div>
      <address class="contact">
        <span class="contact__email">rosaparfrey@mailbox-example.co.nz</span>
        <span class="contact__phone">0218467193</span>
      </address>
    </section>
  </main>
</body>
</html>
```